Fitness website

Website for a fitness brand (see attached specs). Design needs to be modern and vibrant with CTAs on every page. We will provide logos, images, etc but for now user placeholder text and images. For now use the name 'Corvane Athletics' as the name to use on the design. The goal of this site is to either get people to join the gym (5 physical locations across the US); buy an online program; buy merch or supplements or sign up for the newsletter. Pleas use images from this foldeR: https://filebarn.example/share/folders/8QwTz41mKpLrXv93NdYe7HsaBuJ0Cf2_R?usp=sharing

We will be coding this in ReactNative. Lots more work for the winner as well, this is a 1st project for us.

Target Market(s)

fitness enthusiats

Industry/Entity Type

fitness, health, wellness

Number of Pages Required

5+ page

Font styles to use
Other font styles liked:
• Lato

Colors
0054AA
0677BA
7BADD7
CADEEF
E8F1F8
0094D4
00A9DD
6FCCEA
C7EBF8
E9F6FB
00AB8E
00BBA5
67D7C9
C6EFE9
E9F9F6
EE7325
F08F49
F5BC92
FAE3D3
FDF4ED

Requirements
Must have
• must be reactive. most people will view it first on mobile
Nice to have
• video in hero section of top of home page

```html
<!DOCTYPE html>
<html lang="en">
<head>
<meta charset="utf-8">
<title>Corvane Athletics</title>
<link href="https://fonts.googleapis.com/css2?family=Lato:wght@400;700;900&display=swap" rel="stylesheet">
<style>
:root{
  --blue:#033f9b;
  --green:#138a2f;
  --green-soft:#2a9a45;
  --orange:#f04e0c;
  --ink:#111;
  --text:#444;
  --white:#fff;
}
*{margin:0;padding:0;box-sizing:border-box}
html,body{width:1200px;height:4580px;overflow:hidden}
body{position:relative;font-family:'Lato',sans-serif;color:var(--ink);background:var(--white)}
.abs{position:absolute}
.caps{text-transform:uppercase}
.eyebrow{font-weight:900;font-size:20px;color:var(--green);letter-spacing:.2px}
.h2{font-weight:900;font-size:42px;line-height:1.2;text-transform:uppercase}
.btn{display:flex;align-items:center;justify-content:center;color:var(--white);font-weight:700;font-size:18px;background:var(--green);clip-path:polygon(4% 0,100% 0,96% 100%,0 100%)}
.btn.skew-r{clip-path:polygon(0 0,93% 0,100% 100%,5% 100%)}

/* hero */
.hero{left:0;top:0;width:1200px;height:761px;clip-path:polygon(0 0,1200px 0,1200px 658px,0 761px);
  background:radial-gradient(ellipse at 70% 30%,#4a4a4e 0%,#232326 40%,#0b0b0c 80%)}
.logo{left:114px;top:34px;color:var(--white);font-weight:900;font-size:22px;line-height:1.15}
.nav{top:40px;color:var(--white);font-size:17px;font-weight:400}
.nav a{position:absolute;color:var(--white);text-decoration:none;white-space:nowrap}
.nav a.active{color:var(--green-soft)}
.hero-title{left:114px;top:362px;color:var(--white);font-weight:900;font-size:54px;line-height:66px}
.hero-sub{left:114px;top:500px;color:var(--white);font-size:16px}
.play{left:821px;top:337px;width:76px;height:76px}

/* about */
.about-photo{left:114px;top:814px;width:474px;height:478px;clip-path:polygon(0 28px,474px 0,474px 432px,0 478px);
  background:linear-gradient(135deg,#3b3b3d,#1a1a1c 60%,#5a4a40)}
.about-text{left:656px;top:955px;width:460px;border-left:2px solid var(--green);padding-left:16px;font-size:15.5px;line-height:27.5px;color:var(--text);white-space:nowrap}

/* programs */
.band{left:0;width:1200px;background:var(--blue)}
.programs-band{top:1294px;height:943px;clip-path:polygon(0 111px,1200px 0,1200px 831px,0 943px)}
.center{left:0;width:1200px;text-align:center}
.card{width:308px}
.card-photo{width:308px;height:358px;position:relative}
.card-photo .img{position:absolute;inset:0;clip-path:polygon(0 22px,308px 0,308px 336px,0 358px)}
.card-photo svg{position:absolute;left:0;top:0}
.card h3{margin-top:22px;padding-left:22px;color:var(--white);font-weight:900;font-size:21px}
.card p{padding-left:22px;margin-top:10px;color:#e4ebf7;font-size:15px;line-height:26px}
.card a{display:block;padding-left:22px;margin-top:8px;color:var(--white);font-weight:700;font-size:15px;text-decoration:underline}
.arrow{width:36px;height:36px;border-radius:50%;background:var(--white);display:flex;align-items:center;justify-content:center}

/* testimonial */
.quote{left:555px;top:2313px;width:540px;font-size:17px;line-height:30px;color:#333}
.avatar{left:553px;top:2396px;width:54px;height:54px;border-radius:50%;background:linear-gradient(135deg,#9a9ea5,#3c3f45)}
.t-name{left:626px;top:2393px;font-size:26px;color:var(--ink)}
.t-city{left:626px;top:2429px;font-size:14px;color:#555}
.t-arrow{width:38px;height:38px;border-radius:50%;border:1.5px solid #cfd8cf;display:flex;align-items:center;justify-content:center;background:#fff}

/* locations */
.loc-band{top:2533px;height:760px;clip-path:polygon(0 143px,1200px 0,1200px 760px,0 760px)}
.loc{top:2825px;width:181px;height:222px;background:var(--white);text-align:center}
.loc .pic{width:128px;height:128px;border-radius:50%;margin:38px auto 0}
.loc span{display:block;margin-top:20px;font-weight:700;font-size:19px}
.loc.active .pic{box-shadow:0 0 0 3px var(--green)}
.loc.active::after{content:"";position:absolute;left:46px;bottom:-6px;width:90px;height:4px;background:var(--green)}

/* newsletter */
.run-photo{left:0;top:3147px;width:1200px;height:942px;clip-path:polygon(0 143px,1200px 0,1200px 818px,0 942px);
  background:linear-gradient(100deg,#4b4d52 0%,#6a6d72 45%,#8a8d92 65%,#3e4045 100%)}
.news{left:116px;top:3319px;width:496px;height:664px;clip-path:polygon(0 38px,496px 0,496px 628px,0 664px);background:var(--orange)}
.news-frame{left:116px;top:3319px}
.field{left:160px;width:398px;border-bottom:1px solid rgba(255,255,255,.75);color:var(--white);font-size:15px;padding:0 0 16px 15px}
.sub-btn{left:160px;top:3797px;width:432px;height:61px;background:var(--blue);color:var(--white);font-weight:700;font-size:18px;display:flex;align-items:center;justify-content:center;clip-path:polygon(0 0,94% 0,100% 100%,6% 100%)}

/* footer */
.footer{left:0;top:3965px;width:1200px;height:615px;background:var(--blue);clip-path:polygon(0 124px,1200px 0,1200px 615px,0 615px)}
.foot-col{top:4238px;color:var(--white)}
.foot-col h4{font-weight:900;font-size:22px}
.foot-col ul{list-style:none;margin-top:24px}
.foot-col li{font-size:15px;height:42.6px;display:flex;align-items:flex-start;gap:16px}
.foot-col li::before{content:"»";font-size:16px;line-height:17px}
.rule{left:114px;top:4486px;width:972px;height:1px;background:rgba(255,255,255,.25)}
</style>
</head>
<body>

<!-- HERO -->
<div class="abs hero" role="img" aria-label="Athlete jumping rope in a dark training hall, coach kneeling in background"></div>
<div class="abs logo caps">Corvane<br>Athletics</div>
<nav class="abs nav caps" style="left:0;width:1200px">
  <a class="active" style="left:332px">Home</a>
  <a style="left:416px">About</a>
  <a style="left:508px">Programs</a>
  <a style="left:636px">Shop</a>
  <a style="left:715px">Contact</a>
  <a style="left:828px">More</a>
</nav>
<div class="abs btn" style="left:898px;top:25px;width:190px;height:50px;font-size:18px;font-weight:400">Join the Gym</div>
<h1 class="abs hero-title caps">Unleash your<br>inner strength</h1>
<p class="abs hero-sub">Training that transforms. Online. In-gym. Always Corvane.</p>
<div class="abs btn skew-r" style="left:117px;top:544px;width:317px;height:53px">Explore Online Programs</div>
<svg class="abs play" viewBox="0 0 76 76" aria-label="Play video"><circle cx="38" cy="38" r="36" fill="#138a2f" stroke="#0b5a1d" stroke-width="3"/><circle cx="38" cy="38" r="26" fill="none" stroke="#0d6c24" stroke-width="2"/><path d="M31 24 L54 38 L31 52 Z" fill="#fff"/></svg>

<!-- ABOUT -->
<div class="abs about-photo" role="img" aria-label="Athlete in a cap jumping rope during a gym workout"></div>
<div class="abs eyebrow caps" style="left:656px;top:840px">About us</div>
<h2 class="abs h2" style="left:650px;top:875px">Built to break limits</h2>
<p class="abs about-text">Corvane Athletics isn’t just a gym—it’s a movement.<br>From elite coaching to cutting-edge online programs,<br>we help you conquer what you once thought impossible.<br>Whether you train in one of our five U.S. facilities or<br>follow us online, every workout is designed to build<br>stronger bodies and stronger minds.</p>
<div class="abs btn skew-r" style="left:656px;top:1161px;width:316px;height:50px">Find a Location Near You</div>

<!-- PROGRAMS -->
<div class="abs band programs-band"></div>
<div class="abs center eyebrow caps" style="top:1427px;color:var(--green-soft)">Programs</div>
<h2 class="abs center h2" style="top:1463px;color:var(--white)">Your training. Your way.</h2>

<div class="abs arrow" style="left:46px;top:1728px"><svg width="14" height="14" viewBox="0 0 14 14"><path d="M9 2 L4 7 L9 12" fill="none" stroke="#138a2f" stroke-width="2.5"/></svg></div>
<div class="abs arrow" style="left:1106px;top:1728px"><svg width="14" height="14" viewBox="0 0 14 14"><path d="M5 2 L10 7 L5 12" fill="none" stroke="#138a2f" stroke-width="2.5"/></svg></div>

<div class="abs card" style="left:112px;top:1568px">
  <div class="card-photo">
    <div class="img" role="img" aria-label="Athlete on an air bike" style="background:linear-gradient(135deg,#555,#242424 55%,#6b5a50)"></div>
    <svg width="308" height="358"><polyline points="0,22 0,0 308,0" fill="none" stroke="#fff" stroke-width="1.5"/><polyline points="0,358 308,358 308,336" fill="none" stroke="#fff" stroke-width="1.5"/></svg>
  </div>
  <h3 class="caps">Master</h3>
  <p>Sed ut perspiciatis unde omnis iste<br>natus error sit voluptatem accusantium</p>
  <a class="caps">Join now</a>
</div>
<div class="abs card" style="left:446px;top:1568px">
  <div class="card-photo">
    <div class="img" role="img" aria-label="Athlete running in a rig" style="background:linear-gradient(135deg,#6a6a6c,#2c2c2e 55%,#8b7a6c)"></div>
    <svg width="308" height="358"><polyline points="0,22 0,0 308,0" fill="none" stroke="#fff" stroke-width="1.5"/><polyline points="0,358 308,358 308,336" fill="none" stroke="#fff" stroke-width="1.5"/></svg>
  </div>
  <h3 class="caps">Functional fitness</h3>
  <p>Sed ut perspiciatis unde omnis iste<br>natus error sit voluptatem accusantium</p>
  <a class="caps">Join now</a>
</div>
<div class="abs card" style="left:782px;top:1568px">
  <div class="card-photo">
    <div class="img" role="img" aria-label="Athlete holding a barbell overhead" style="background:linear-gradient(135deg,#4a4e58,#1f2126 55%,#7c6f66)"></div>
    <svg width="308" height="358"><polyline points="0,22 0,0 308,0" fill="none" stroke="#fff" stroke-width="1.5"/><polyline points="0,358 308,358 308,336" fill="none" stroke="#fff" stroke-width="1.5"/></svg>
  </div>
  <h3 class="caps">Competitive</h3>
  <p>Sed ut perspiciatis unde omnis iste<br>natus error sit voluptatem accusantium</p>
  <a class="caps">Join now</a>
</div>

<!-- TESTIMONIAL -->
<div class="abs eyebrow caps" style="left:114px;top:2314px">Testimonial</div>
<h2 class="abs h2" style="left:111px;top:2352px;font-size:44px;line-height:55px">What<br>our client say</h2>
<p class="abs quote">The coaches at Corvane completely changed how I see fitness.<br>I’m stronger than ever.</p>
<div class="abs avatar" role="img" aria-label="Client portrait"></div>
<div class="abs t-name">Dana R</div>
<div class="abs t-city">San Diego</div>
<div class="abs t-arrow" style="left:987px;top:2404px"><svg width="14" height="14" viewBox="0 0 14 14"><path d="M9 2 L4 7 L9 12" fill="none" stroke="#138a2f" stroke-width="2.5"/></svg></div>
<div class="abs t-arrow" style="left:1044px;top:2404px"><svg width="14" height="14" viewBox="0 0 14 14"><path d="M5 2 L10 7 L5 12" fill="none" stroke="#138a2f" stroke-width="2.5"/></svg></div>

<!-- LOCATIONS -->
<div class="abs band loc-band"></div>
<div class="abs center eyebrow caps" style="top:2687px;color:var(--green-soft)">Locations</div>
<h2 class="abs center h2" style="top:2728px;color:var(--white)">Train with us nationwide</h2>
<div class="abs loc" style="left:112px"><div class="pic" role="img" aria-label="San Diego skyline at sunset" style="background:linear-gradient(180deg,#e98a55,#b5654a 55%,#3c3a40)"></div><span>San Diego</span></div>
<div class="abs loc active" style="left:311px"><div class="pic" role="img" aria-label="Boston city view with autumn trees" style="background:linear-gradient(180deg,#9fb6c9,#b9a27c 50%,#b85a28)"></div><span>Boston</span></div>
<div class="abs loc" style="left:510px"><div class="pic" role="img" aria-label="Miami beach and waterfront aerial" style="background:linear-gradient(135deg,#6fc3d8,#9bb59a 50%,#4f7e5a)"></div><span>Miami</span></div>
<div class="abs loc" style="left:708px"><div class="pic" role="img" aria-label="Seattle skyline with observation tower" style="background:linear-gradient(180deg,#8fb2d6,#4d6f93 55%,#2b3b52)"></div><span>Seattle</span></div>
<div class="abs loc" style="left:907px"><div class="pic" role="img" aria-label="Capitol building at dusk" style="background:linear-gradient(180deg,#2c3e78,#5a6ea0 55%,#c8a36e)"></div><span>Dc</span></div>

<!-- NEWSLETTER -->
<div class="abs run-photo" role="img" aria-label="Athlete in light blue outfit running through an arena"></div>
<div class="abs news"></div>
<svg class="abs news-frame" width="500" height="670" viewBox="0 0 500 670">
  <polyline points="0,86 0,0 222,21" fill="none" stroke="#fff" stroke-width="1.5"/>
  <polyline points="258,644 496,664 496,585" fill="none" stroke="#fff" stroke-width="1.5"/>
</svg>
<div class="abs eyebrow caps" style="left:158px;top:3443px;color:var(--white)">Newsletter signup</div>
<h2 class="abs h2" style="left:157px;top:3485px;color:var(--white);font-size:42px">Stay invincible</h2>
<p class="abs" style="left:158px;top:3552px;color:var(--white);font-size:16px;line-height:27px">Join thousands of athletes who get exclusive<br>training tips, new program alerts, and insider deals.</p>
<div class="abs field" style="top:3643px">Name</div>
<div class="abs field" style="top:3714px">Email</div>
<div class="abs sub-btn">Subscribe Now</div>

<!-- FOOTER -->
<div class="abs footer"></div>
<div class="abs center caps" style="top:4125px;color:var(--white);font-weight:900;font-size:44px">Corvane Athletics</div>
<div class="abs foot-col" style="left:164px"><h4 class="caps">Company</h4><ul class="caps"><li>About us</li><li>Locations</li><li>Careers</li><li>Contact</li></ul></div>
<div class="abs foot-col" style="left:517px"><h4 class="caps">Programs</h4><ul class="caps"><li>Join a gym</li><li>Online training</li><li>Private coaching</li></ul></div>
<div class="abs foot-col" style="left:896px"><h4 class="caps">Follow us</h4><ul class="caps"><li>Loopcast</li><li>Viewnest</li><li>Circlefeed</li><li>Clipwave</li></ul></div>
<div class="abs rule"></div>
<div class="abs center" style="top:4519px;color:var(--white);font-size:15px">© 2025 Corvane Athletics. All Rights Reserved.</div>

</body>
</html>
```